Veltrano.co - Polar Expeditions Specialists

We need a modern, visually striking business card for Veltrano.co, a company specialized in selling expedition cruises to the most remote regions on Earth, with a focus on the Arctic and Antarctica. The design should instantly communicate that the cardholder is an expert in polar travel. Use clean, premium aesthetics with cool tones like icy blue and white, possibly incorporating polar imagery (ice, glaciers, penguins, etc.)

Attached the logo

Contact Information for Business Card

Feels high-end and trustworthy.. Visually memorable — encourages people to keep it

Colors
0054AA
0677BA
7BADD7
CADEEF
E8F1F8

Requirements
Must have
• ice, glaciers, penguins, montains
Nice to have
• modern, transparente,

```html
<!DOCTYPE html>
<html lang="en">
<head>
<meta charset="utf-8">
<title>Veltrano.co – Business Card</title>
<link href="https://fonts.googleapis.com/css2?family=Poppins:wght@400;500;600;700&display=swap" rel="stylesheet">
<style>
  :root{
    --backdrop:#2a2b2e;
    --brand:#2F6FAD;
    --brand-faint:rgba(123,173,215,0.35);
    --paper:#ffffff;
    --ink:#1d1d1f;
    --ice:#E8F1F8;
  }
  *{margin:0;padding:0;box-sizing:border-box;}
  html,body{width:1200px;height:900px;overflow:hidden;}
  body{background:var(--backdrop);font-family:'Poppins',sans-serif;position:relative;}

  .card{position:absolute;left:250px;width:700px;height:400px;border-radius:26px;overflow:hidden;}
  .card--front{top:35px;background:var(--brand);color:var(--paper);}
  .card--back{top:465px;background:var(--paper);color:var(--ink);}

  /* front */
  .front__deco{position:absolute;right:-70px;bottom:-90px;width:380px;height:380px;border-radius:50%;background:var(--brand-faint);}
  .front__brand{position:absolute;left:0;right:0;top:110px;text-align:center;}
  .front__mark{display:block;width:64px;height:64px;border-radius:50%;background:var(--paper);margin:0 auto 14px;}
  .front__name{font-weight:700;font-size:76px;line-height:1;letter-spacing:1px;}
  .front__tagline{font-weight:600;font-size:22px;margin-top:12px;letter-spacing:.3px;}

  /* back */
  .back__brand{position:absolute;left:60px;top:52px;display:flex;align-items:center;gap:26px;color:var(--brand);}
  .back__mark{width:92px;height:92px;border-radius:50%;background:var(--brand);flex:none;}
  .back__name{font-weight:700;font-size:72px;line-height:1;letter-spacing:1px;}
  .back__tagline{font-weight:600;font-size:21px;margin-top:8px;}

  .person{position:absolute;left:60px;top:218px;width:230px;text-align:right;}
  .person__name{font-weight:700;font-size:30px;color:var(--brand);line-height:1.1;}
  .person__role{font-size:17px;margin-top:2px;}

  .divider{position:absolute;left:312px;top:222px;width:2px;height:62px;background:var(--ink);}

  .contacts{position:absolute;left:336px;top:218px;list-style:none;font-size:18px;line-height:1.5;}
  .contacts li{display:flex;align-items:center;gap:10px;}
  .contacts svg{width:15px;height:15px;fill:var(--brand);flex:none;}

  .address{position:absolute;left:60px;right:40px;top:326px;font-size:18px;}
</style>
</head>
<body>

<section class="card card--front" aria-label="Card front">
  <div class="front__deco" aria-hidden="true"></div>
  <div class="front__brand">
    <span class="front__mark" aria-hidden="true"></span>
    <div class="front__name">Veltrano.co</div>
    <div class="front__tagline">Polar Expeditions Specialists</div>
  </div>
</section>

<section class="card card--back" aria-label="Card back">
  <div class="back__brand">
    <span class="back__mark" aria-hidden="true"></span>
    <div>
      <div class="back__name">Veltrano.co</div>
      <div class="back__tagline">Polar Expeditions Specialists</div>
    </div>
  </div>

  <div class="person">
    <div class="person__name">Marlow Teague</div>
    <div class="person__role">CEO &amp; Founder</div>
  </div>

  <div class="divider" aria-hidden="true"></div>

  <ul class="contacts">
    <li><svg viewBox="0 0 24 24" aria-hidden="true"><path d="M6.6 10.8a15.1 15.1 0 0 0 6.6 6.6l2.2-2.2c.3-.3.7-.4 1-.2 1.1.4 2.3.6 3.6.6.6 0 1 .4 1 1V20c0 .6-.4 1-1 1A17 17 0 0 1 3 4c0-.6.4-1 1-1h3.5c.6 0 1 .4 1 1 0 1.3.2 2.5.6 3.6.1.3 0 .7-.2 1z"/></svg>+1.555.014.782</li>
    <li><svg viewBox="0 0 24 24" aria-hidden="true"><path d="M2 5h20v14H2z M2 5l10 8 10-8" /></svg>hello@veltrano.co</li>
    <li><svg viewBox="0 0 24 24" aria-hidden="true"><circle cx="12" cy="12" r="10"/></svg>www.veltrano.co</li>
  </ul>

  <div class="address">42 Harbor Crest Lane, Ashford, NJ 07811 USA</div>
</section>

</body>
</html>
```